Construction business card

I need a new business card, they can connect with my logo, brand.
What we do is residential house , design and build
I like: Navy blue / black
I attached our logo, brand,
and, some idea for business card.

```html
<!DOCTYPE html>
<html lang="en">
<head>
<meta charset="utf-8">
<title>Norvane Building Group – Business Card</title>
<link rel="stylesheet" href="https://fonts.googleapis.com/css2?family=Montserrat:wght@400;500;600;700&display=swap">
<style>
  :root {
    --stage: #2a2a2a;
    --paper: #f7f7f6;
    --brand-blue: #4f86d4;
    --ink: #3a3b3f;
    --back-deep: #0064ad;
    --back-light: #00a9da;
    --back-mark: #0d8fd0;
  }
  * { margin: 0; padding: 0; box-sizing: border-box; }
  html, body {
    width: 1200px; height: 825px; overflow: hidden;
    background: var(--stage);
    font-family: "Montserrat", sans-serif;
  }
  .stage {
    width: 1200px; height: 825px;
    display: flex; align-items: center; justify-content: center; gap: 40px;
  }
  .card {
    position: relative;
    width: 560px; height: 320px;
    overflow: hidden;
  }

  /* Back of card */
  .card--back {
    background: linear-gradient(100deg, var(--back-deep) 0%, var(--back-light) 100%);
    display: flex; align-items: center; justify-content: center;
  }
  .back-wordmark {
    font-weight: 700; font-size: 30px; letter-spacing: 1px;
    text-transform: uppercase; color: var(--back-mark);
    text-align: center; line-height: 1.2;
  }

  /* Front of card */
  .card--front { background: var(--paper); color: var(--ink); }
  .accent-square {
    position: absolute; left: 26px; top: 150px;
    width: 16px; height: 30px; background: var(--brand-blue);
  }
  .identity { position: absolute; left: 70px; top: 128px; }
  .identity__name {
    font-weight: 700; font-size: 22px; letter-spacing: .5px;
    color: var(--brand-blue); text-transform: uppercase;
  }
  .identity__role { font-size: 15px; font-weight: 500; margin-top: 2px; }

  .address {
    position: absolute; left: 110px; top: 205px;
    font-size: 13.5px; line-height: 1.35; font-style: normal;
  }
  .contacts {
    position: absolute; left: 88px; top: 247px;
    list-style: none; font-size: 13.5px; line-height: 1.35;
  }
  .contacts li { display: flex; align-items: center; gap: 9px; }
  .contacts svg { width: 13px; height: 13px; fill: var(--brand-blue); flex: none; }

  .wordmark {
    position: absolute; right: 34px; top: 58px;
    display: flex; align-items: center; gap: 10px;
  }
  .wordmark__square { width: 18px; height: 18px; background: var(--brand-blue); }
  .wordmark__name {
    font-weight: 700; font-size: 20px; line-height: 1.15;
    color: var(--brand-blue); text-transform: uppercase; letter-spacing: .5px;
  }
</style>
</head>
<body>
<main class="stage">
  <section class="card card--back" aria-label="Card back">
    <p class="back-wordmark">Norvane<br>Building Group</p>
  </section>

  <section class="card card--front" aria-label="Card front">
    <div class="accent-square"></div>

    <div class="wordmark">
      <span class="wordmark__square"></span>
      <span class="wordmark__name">Norvane<br>Building Group</span>
    </div>

    <div class="identity">
      <h1 class="identity__name">Dalia Verhoef</h1>
      <p class="identity__role">Founder &amp; CEO</p>
    </div>

    <address class="address">48 Ashcombe St,<br>Elmvale, VIC 3920</address>

    <ul class="contacts">
      <li>
        <svg viewBox="0 0 24 24" aria-hidden="true"><path d="M6.6 10.8a15.1 15.1 0 0 0 6.6 6.6l2.2-2.2a1 1 0 0 1 1-.25 11.4 11.4 0 0 0 3.6.57 1 1 0 0 1 1 1V20a1 1 0 0 1-1 1A17 17 0 0 1 3 4a1 1 0 0 1 1-1h3.5a1 1 0 0 1 1 1c0 1.25.2 2.45.57 3.6a1 1 0 0 1-.25 1z"/></svg>
        0400 555 018
      </li>
      <li>
        <svg viewBox="0 0 24 24" aria-hidden="true"><path d="M2 5h20v14H2z M2 5l10 8 10-8" fill="none" stroke="#4f86d4" stroke-width="2.5"/></svg>
        info@norvanebuilding.com.au
      </li>
      <li>
        <svg viewBox="0 0 24 24" aria-hidden="true"><circle cx="12" cy="12" r="10"/><path d="M2 12h20M12 2c3 3 3 17 0 20M12 2c-3 3-3 17 0 20" fill="none" stroke="#f7f7f6" stroke-width="1.5"/></svg>
        www.norvanebuilding.com.au
      </li>
    </ul>
  </section>
</main>
</body>
</html>
```